Street Sign Project - Attract Customers

We need a street sign designed to display out the front of the building. It design will need to be 1800mm wide x 900mm high. We need to show potential customers where we are inviting. Some of the attachments are for inspiration. The sign will be printed on a sheet of aluminum. if you have a good look at our web site which is www.tv-r.com.au you should get a good feeling about the company and what we do.

Target Market(s)

Construction companies, landscaping and civil earth moving companies who may drive past our business

Industry/Entity Type

Building

Font styles to use
Sans Serif

Colors
ffffff
3277b5
000000

Requirements
Must have
• Company logo must be the main focus point
• The number "38" on the sign to show street number (300mm high)
• phone number - (02) 9413 5860
• web address - www.tv-r.com.au
• I have loaded pictures i would like to see used in the sign
Nice to have
• Banner picture as attached
Should not have
• Bright colours. Please use our blue colour where possible

```html
<!DOCTYPE html>
<html lang="en">
<head>
<meta charset="utf-8">
<title>Lifting &amp; Loading Systems – Street Sign</title>
<link rel="stylesheet" href="https://fonts.googleapis.com/css2?family=Arimo:wght@700&display=swap">
<style>
  :root {
    --brand-blue: #3277b5;
    --bright-blue: #1e88d0;
    --pale-blue: #cfe2f2;
    --white: #ffffff;
    --black: #000000;
    --photo-steel: #8fa7bd;
    --photo-roof: #a9bfd6;
    --photo-rubble: #a89a86;
    --photo-scaffold: #7d93ad;
  }
  html, body {
    margin: 0;
    padding: 0;
    overflow: hidden;
    background: var(--white);
  }
  .sign {
    position: relative;
    width: 1200px;
    height: 600px;
    overflow: hidden;
    background: var(--white);
    font-family: "Arimo", Arial, sans-serif;
  }
  .building-backdrop {
    position: absolute;
    left: 0;
    top: 0;
    width: 400px;
    height: 600px;
    background: linear-gradient(90deg, rgba(120,160,200,0.55) 0%, rgba(190,212,232,0.35) 55%, rgba(255,255,255,0) 100%);
  }
  .bands {
    position: absolute;
    inset: 0;
  }
  .brand {
    position: absolute;
    right: 24px;
    top: 16px;
    display: flex;
    align-items: center;
    gap: 14px;
    color: var(--bright-blue);
    font-weight: 700;
    font-size: 38px;
    line-height: 38px;
    letter-spacing: 0.5px;
    text-transform: uppercase;
    text-align: center;
  }
  .brand-mark {
    width: 26px;
    height: 26px;
    background: var(--bright-blue);
  }
  .gallery {
    position: absolute;
    top: 169px;
    left: 136px;
    display: flex;
    gap: 12px;
  }
  .gallery-photo {
    height: 267px;
  }
  .photo-hoist { width: 222px; background: linear-gradient(160deg, #eef1f4, var(--photo-steel)); }
  .photo-roof { width: 234px; background: linear-gradient(180deg, #7fb2e0 0%, var(--photo-roof) 40%, #b8866c 60%, #7fa060 100%); }
  .photo-rubble { width: 230px; background: linear-gradient(170deg, #8b7a5e, var(--photo-rubble) 60%, #c9bba8); }
  .photo-lift { width: 231px; background: linear-gradient(180deg, #c9a28a, var(--photo-scaffold) 60%, #3d6fb0); }
  .street-address {
    position: absolute;
    left: 336px;
    top: 452px;
    margin: 0;
    color: var(--bright-blue);
    font-size: 45px;
    font-weight: 700;
    line-height: 70px;
    letter-spacing: 0.5px;
  }
  .street-number {
    font-size: 66px;
  }
  .contact {
    position: absolute;
    right: 22px;
    top: 515px;
    text-align: right;
    color: var(--white);
    font-weight: 700;
    letter-spacing: 1px;
  }
  .contact-phone { font-size: 35px; line-height: 40px; }
  .contact-web { font-size: 30px; line-height: 36px; }
</style>
</head>
<body>
<div class="sign">
  <div class="building-backdrop" role="img" aria-label="Faded blue-tinted photo of a multi-storey building with a rubbish chute"></div>

  <svg class="bands" width="1200" height="600" viewBox="0 0 1200 600" aria-hidden="true">
    <polygon points="0,0 636,0 0,172" fill="var(--bright-blue)"/>
    <polygon points="0,172 636,0 660,0 0,180" fill="var(--white)"/>
    <polygon points="0,180 660,0 700,0 0,195" fill="var(--pale-blue)" opacity="0.7"/>
    <polygon points="520,600 1200,408 1200,420 560,600" fill="var(--pale-blue)"/>
    <polygon points="560,600 1200,420 1200,600" fill="var(--bright-blue)"/>
  </svg>

  <div class="brand">
    <span class="brand-mark"></span>
    <span class="brand-name">Lifting<br>&amp; Loading<br>Systems</span>
  </div>

  <div class="gallery">
    <div class="gallery-photo photo-hoist" role="img" aria-label="Worker operating a material hoist on scaffolding"></div>
    <div class="gallery-photo photo-roof" role="img" aria-label="Ladder hoist running up to a tiled roof with solar panels"></div>
    <div class="gallery-photo photo-rubble" role="img" aria-label="Worker beside a conveyor moving rubble on a site"></div>
    <div class="gallery-photo photo-lift" role="img" aria-label="Blue construction lift mounted on scaffolding"></div>
  </div>

  <p class="street-address"><span class="street-number">38</span> Brennock Street</p>

  <div class="contact">
    <div class="contact-phone">(02) 9413 5860</div>
    <div class="contact-web">www.tv-r.com.au</div>
  </div>
</div>
</body>
</html>
```